Natural Medicine & Health/Fitness Coaching studio requires web page

Require a innovative web page for a studio that coaches clients to better health, nutrition and fitness. The studio compromises of Clinical Nutritionists, Naturopaths, Rehab Trainers, Personal Trainers and Sport Coaches. Would like to see earthy but bold designs emphasizing nutritional health and athletic performance.
Updates

Design only launched today.

Target Market(s)

All genders from 20's to 60's, as well as families

Industry/Entity Type

Nutritionist

Coding

Coded - Design and coding required

Number of Pages Required

3 page

Colors
abd037
3277b5
fbee3d
fece3e
33b8a4
f04a50

Requirements
Must have
• Online booking system, ability to message
• Home page
• Coaching/Fitness page
• Nutritional Medicine page
• Must be suitable for both Fitness and Nutrition

```html
<!DOCTYPE html>
<html lang="en">
<head>
<meta charset="utf-8">
<title>Evergrove Fit – Nutritional Therapy</title>
<link href="https://fonts.googleapis.com/css2?family=Montserrat:wght@400;500;600;700;800&display=swap" rel="stylesheet">
<style>
:root{
  --green:#8cc63f;
  --green-dark:#7ab22e;
  --blue:#1a5585;
  --blue-band:#17527f;
  --ink:#333;
  --muted:#666;
  --black:#121212;
  --white:#fff;
  --star:#f7941d;
}
*{box-sizing:border-box;margin:0;padding:0}
html,body{width:1200px;height:4401px;overflow:hidden}
body{position:relative;font-family:"Montserrat",sans-serif;color:var(--ink);background:var(--white)}
.abs{position:absolute}
.header{left:0;top:0;width:1200px;height:115px;background:var(--white)}
.brand{left:78px;top:24px;font-size:40px;font-weight:700;color:var(--green-dark);line-height:1}
.brand-sub{left:118px;top:72px;font-size:14px;font-weight:600;color:var(--blue)}
.topbar{left:645px;top:0;height:34px;display:flex;font-size:14px;font-weight:600;color:var(--white)}
.topbar .book{background:var(--blue);width:190px;display:flex;align-items:center;justify-content:center;border-radius:0 0 0 14px}
.topbar .phone{background:var(--green);width:196px;display:flex;align-items:center;justify-content:center;gap:8px;border-radius:0 0 14px 0}
.nav{left:565px;top:70px;display:flex;gap:38px;font-size:14px;font-weight:500;color:#222}
.nav .active{color:var(--blue)}
.hero{left:0;top:115px;width:1200px;height:640px;overflow:hidden}
.hero-photo{position:absolute;inset:0;background:linear-gradient(100deg,#151515 0%,#2b2b2b 45%,#5a4a40 70%,#2a2a2a 100%)}
.hero h1{left:80px;top:170px;color:var(--white);font-size:54px;font-weight:700;line-height:1.05}
.hero h1 span{display:block;font-size:46px}
.hero p{left:80px;top:318px;width:440px;color:var(--white);font-size:14px;font-weight:500;line-height:1.6}
.btn{display:inline-flex;align-items:center;justify-content:center;font-size:15px;font-weight:600;color:var(--white)}
.btn-green{background:var(--green);border-radius:24px}
.btn-blue{background:var(--blue)}
.dots{left:1140px;top:260px;display:flex;flex-direction:column;align-items:center;gap:16px}
.dots i{display:block;width:12px;height:12px;border-radius:50%;background:var(--white)}
.dots i.on{width:26px;height:26px;border:3px solid var(--white);background:transparent;position:relative}
.dots i.on::after{content:"";position:absolute;inset:5px;border-radius:50%;background:var(--white)}
.photo{background:linear-gradient(135deg,#c7b29c,#6e5a4d)}
h2.section{font-size:36px;font-weight:700;color:var(--blue)}
h3.service{font-size:32px;font-weight:700;color:var(--green-dark)}
.copy{font-size:14px;line-height:1.95;color:var(--muted);text-align:justify}
.badge{width:90px;height:90px;border-radius:50%;background:var(--white)}
.band{left:0;top:2730px;width:1200px;height:565px;background:var(--blue-band);color:var(--white)}
.band h2{position:absolute;left:0;width:1200px;top:90px;text-align:center;font-size:40px;font-weight:700}
.team{position:absolute;top:200px;width:250px;text-align:center}
.team .ring{width:128px;height:128px;margin:0 auto;border:3px solid var(--white);border-radius:50%;display:flex;align-items:center;justify-content:center}
.team h4{margin-top:30px;font-size:18px;font-weight:700}
.team p{margin-top:14px;font-size:13px;line-height:1.7}
.arrow{position:absolute;top:295px;width:52px;height:52px;border-radius:50%;background:var(--white);display:flex;align-items:center;justify-content:center}
.testi{top:3355px;left:0;width:1200px}
.card{position:absolute;top:3560px;width:295px;height:180px;background:var(--white);box-shadow:0 4px 18px rgba(0,0,0,.18);padding:56px 30px 0;text-align:center;font-size:12.5px;line-height:1.75;color:var(--muted)}
.avatar{position:absolute;top:3508px;width:88px;height:88px;border-radius:50%;border:4px solid var(--white);background:linear-gradient(135deg,#b79784,#5b4339);box-shadow:0 2px 8px rgba(0,0,0,.2)}
.who{position:absolute;top:3758px;width:295px;text-align:center;color:var(--blue);font-weight:600;font-size:15px;line-height:1.5}
.who .stars{color:var(--star);letter-spacing:3px;font-size:15px}
.footer{left:0;top:3880px;width:1200px;height:521px}
.footer-body{position:absolute;left:0;top:120px;width:1200px;height:401px;background:var(--black);color:var(--white)}
.f-brand{left:75px;top:150px;font-size:40px;font-weight:700;color:var(--white)}
.f-sub{left:120px;top:198px;font-size:14px;font-weight:500;color:var(--white)}
.footer h5{position:absolute;top:100px;font-size:20px;font-weight:500}
.f-news{left:420px;top:140px;width:170px;font-size:11px;line-height:1.6}
.f-field{left:420px;top:228px;width:160px;font-size:11px;border-bottom:1px solid #777;padding-bottom:6px}
.f-sign{left:420px;top:268px;width:100px;height:32px;font-size:12px}
.f-links{left:672px;top:142px;list-style:none;font-size:12px;font-weight:600;line-height:1.85}
.f-contact{left:862px;top:140px;font-size:13px;line-height:1.5}
.f-contact div{display:flex;gap:16px;align-items:flex-start;margin-bottom:26px}
.copyright{left:75px;top:478px;font-size:11px;font-weight:600}
.social{left:903px;top:465px;display:flex;gap:14px}
.social i{display:block;width:22px;height:22px;border-radius:50%;background:#333}
.social i.on{background:var(--green)}
.page-code{left:1155px;top:490px;font-size:10px;color:#aaa}
</style>
</head>
<body>

<header class="header abs">
  <div class="brand abs">Evergrove Fit</div>
  <div class="brand-sub abs">Nutritional Therapy</div>
  <div class="topbar abs">
    <div class="book">Online Booking</div>
    <div class="phone">
      <svg width="14" height="14" viewBox="0 0 24 24"><path fill="#fff" d="M6.6 10.8a15 15 0 0 0 6.6 6.6l2.2-2.2a1 1 0 0 1 1-.25 11.4 11.4 0 0 0 3.6.57 1 1 0 0 1 1 1V20a1 1 0 0 1-1 1A17 17 0 0 1 3 4a1 1 0 0 1 1-1h3.5a1 1 0 0 1 1 1c0 1.25.2 2.45.57 3.57a1 1 0 0 1-.25 1z"/></svg>
      (555) 013 2046
    </div>
  </div>
  <nav class="nav abs">
    <span class="active">Home</span><span>About Us</span><span>Coaching</span><span>Fitness</span><span>Nutrition</span><span>Contact Us</span>
  </nav>
</header>

<section class="hero abs">
  <div class="hero-photo" role="img" aria-label="Athlete drinking from a shaker bottle in a dark gym"></div>
  <h1 class="abs">Evergrove Fit<span>Nutritional Therapy</span></h1>
  <p class="abs">Lorem ipsum dolor sit amet, consectetur adipiscing elit, sed do eiusmod tempor incididunt ut labore et dolore magna aliqua.</p>
  <a class="btn btn-green abs" style="left:82px;top:396px;width:165px;height:42px">Read More</a>
  <div class="dots abs"><i class="on"></i><i></i><i></i></div>
  <svg class="abs" style="left:0;top:440px" width="1200" height="200" viewBox="0 0 1200 200" preserveAspectRatio="none">
    <path d="M0 175 C 250 110, 600 20, 1200 95 L1200 200 L0 200Z" fill="#1a5585"/>
    <path d="M0 190 C 300 120, 650 55, 1200 112 L1200 200 L0 200Z" fill="#8cc63f"/>
    <path d="M0 200 C 320 135, 680 80, 1200 132 L1200 200Z" fill="#fff"/>
  </svg>
</section>

<section class="about">
  <div class="abs" style="left:90px;top:900px;width:350px;height:400px;background:var(--blue)"></div>
  <div class="abs photo" style="left:115px;top:875px;width:350px;height:400px" role="img" aria-label="Smiling couple holding dumbbells"></div>
  <h2 class="section abs" style="left:555px;top:898px">About Us</h2>
  <p class="copy abs" style="left:555px;top:958px;width:565px">Sed ut perspiciatis unde omnis iste natus error sit voluptatem accusantium doloremque laudantium, totam rem aperiam, eaque ipsa quae ab illo inventore veritatis et quasi architecto beatae vitae dicta sunt explicabo. Nemo enim ipsam voluptatem quia voluptas sit aspernatur aut odit aut fugit, sed quia consequuntur magni dolores eos qui ratione voluptatem sequi nesciunt. Neque porro quisquam est, qui dolorem ipsum quia dolor sit amet, consectetur, adipisci velit, sed quia non numquam eius modi tempora incidunt ut labore et dolore magnam aliquam quaerat voluptatem.</p>
  <a class="btn btn-blue abs" style="left:555px;top:1195px;width:155px;height:44px">Read More</a>
</section>

<section class="service-nutrition">
  <h3 class="service abs" style="left:78px;top:1458px">Nutrition Services</h3>
  <p class="copy abs" style="left:78px;top:1510px;width:505px">Sed ut perspiciatis unde omnis iste natus error sit voluptatem accusantium doloremque laudantium, totam rem aperiam, eaque ipsa quae ab illo inventore veritatis et quasi architecto beatae vitae dicta sunt explicabo. Nemo enim ipsam voluptatem quia voluptas sit aspernatur aut odit aut fugit, sed quia consequuntur magni dolores eos qui ratione voluptatem sequi nesciunt. Neque porro quisquam est, qui dolorem ipsum quia dolor sit amet</p>
  <a class="btn btn-blue abs" style="left:78px;top:1725px;width:177px;height:55px">Read More</a>
  <div class="abs" style="left:662px;top:1465px;width:456px;height:320px;background:linear-gradient(135deg,#9ccc3c,#5f9a22)" role="img" aria-label="Woman eating a salad on a green picnic blanket"></div>
  <div class="badge abs" style="left:662px;top:1695px"></div>
</section>

<section class="service-fitness">
  <div class="abs photo" style="left:78px;top:1878px;width:455px;height:320px;background:linear-gradient(135deg,#e8e2da,#8f8c88)" role="img" aria-label="Woman lifting dumbbells on a bench"></div>
  <div class="badge abs" style="left:443px;top:2108px"></div>
  <h3 class="service abs" style="left:612px;top:1870px">Fitness Services</h3>
  <p class="copy abs" style="left:612px;top:1922px;width:505px">Sed ut perspiciatis unde omnis iste natus error sit voluptatem accusantium doloremque laudantium, totam rem aperiam, eaque ipsa quae ab illo inventore veritatis et quasi architecto beatae vitae dicta sunt explicabo. Nemo enim ipsam voluptatem quia voluptas sit aspernatur aut odit aut fugit, sed quia consequuntur magni dolores eos qui ratione voluptatem sequi nesciunt. Neque porro quisquam est, qui dolorem ipsum quia dolor sit amet</p>
  <a class="btn btn-blue abs" style="left:612px;top:2137px;width:177px;height:55px">Read More</a>
</section>

<section class="service-online">
  <h3 class="service abs" style="left:78px;top:2282px">Mobile and Online Services</h3>
  <p class="copy abs" style="left:78px;top:2334px;width:505px">Sed ut perspiciatis unde omnis iste natus error sit voluptatem accusantium doloremque laudantium, totam rem aperiam, eaque ipsa quae ab illo inventore veritatis et quasi architecto beatae vitae dicta sunt explicabo. Nemo enim ipsam voluptatem quia voluptas sit aspernatur aut odit aut fugit, sed quia consequuntur magni dolores eos qui ratione voluptatem sequi nesciunt. Neque porro quisquam est, qui dolorem ipsum quia dolor sit amet</p>
  <a class="btn btn-blue abs" style="left:78px;top:2550px;width:177px;height:55px">Read More</a>
  <div class="abs" style="left:662px;top:2288px;width:456px;height:322px;background:linear-gradient(135deg,#f1ece6,#c9b9ab)" role="img" aria-label="Women planning meals at a desk with a laptop"></div>
  <div class="badge abs" style="left:662px;top:2520px"></div>
</section>

<section class="band abs">
  <h2>The Studio Compromises</h2>
  <div class="arrow" style="left:42px"><svg width="18" height="18" viewBox="0 0 24 24"><path d="M15 4 7 12l8 8" fill="none" stroke="#333" stroke-width="3"/></svg></div>
  <div class="arrow" style="left:1106px"><svg width="18" height="18" viewBox="0 0 24 24"><path d="m9 4 8 8-8 8" fill="none" stroke="#333" stroke-width="3"/></svg></div>
  <div class="team" style="left:75px">
    <div class="ring"><svg width="56" height="56" viewBox="0 0 56 56" fill="none" stroke="#fff" stroke-width="2.5"><rect x="12" y="8" width="32" height="40" rx="3"/><path d="M20 20h16M20 28h16M20 36h10"/></svg></div>
    <h4>Clinical Nutritionists</h4><p>Sed ut perspiciatis unde omnis<br>iste natus error sit voluptatem<br>accusantium</p>
  </div>
  <div class="team" style="left:338px">
    <div class="ring"><svg width="56" height="56" viewBox="0 0 56 56" fill="none" stroke="#fff" stroke-width="2.5"><circle cx="28" cy="28" r="20"/><circle cx="28" cy="28" r="12"/><circle cx="28" cy="28" r="4"/><path d="M28 28 46 10"/></svg></div>
    <h4>Sport Coaches</h4><p>Sed ut perspiciatis unde omnis<br>iste natus error sit voluptatem<br>accusantium</p>
  </div>
  <div class="team" style="left:598px">
    <div class="ring"><svg width="56" height="56" viewBox="0 0 56 56" fill="none" stroke="#fff" stroke-width="2.5"><circle cx="28" cy="14" r="6"/><path d="M28 20v14M18 26h20M28 34l-8 12M28 34l8 12"/></svg></div>
    <h4>Naturopaths</h4><p>Sed ut perspiciatis unde omnis<br>iste natus error sit voluptatem<br>accusantium</p>
  </div>
  <div class="team" style="left:860px">
    <div class="ring"><svg width="56" height="56" viewBox="0 0 56 56" fill="none" stroke="#fff" stroke-width="2.5"><circle cx="28" cy="20" r="9"/><path d="M12 46c2-10 9-15 16-15s14 5 16 15z"/></svg></div>
    <h4>Personal Trainers</h4><p>Sed ut perspiciatis unde omnis<br>iste natus error sit voluptatem<br>accusantium</p>
  </div>
</section>

<section class="testimonials">
  <h2 class="section abs" style="left:0;top:3380px;width:1200px;text-align:center;font-size:40px">Client Testimonials</h2>
  <div class="card" style="left:118px">Sed ut perspiciatis unde omnis iste natus error sit voluptatem accusantium doloremque laudantium, totam rem aperiam, eaque ipsa</div>
  <div class="card" style="left:453px">Sed ut perspiciatis unde omnis iste natus error sit voluptatem accusantium doloremque laudantium, totam rem aperiam, eaque ipsa</div>
  <div class="card" style="left:788px">Sed ut perspiciatis unde omnis iste natus error sit voluptatem accusantium doloremque laudantium, totam rem aperiam, eaque ipsa</div>
  <div class="avatar" role="img" aria-label="Client portrait" style="left:221px"></div>
  <div class="avatar" role="img" aria-label="Client portrait" style="left:556px"></div>
  <div class="avatar" role="img" aria-label="Client portrait" style="left:891px"></div>
  <div class="who" style="left:118px">Sam Rivera<br>Summit Physio Clinic<br><span class="stars">★★★★★</span></div>
  <div class="who" style="left:453px">Sam Rivera<br>Summit Physio Clinic<br><span class="stars">★★★★★</span></div>
  <div class="who" style="left:788px">Sam Rivera<br>Summit Physio Clinic<br><span class="stars">★★★★★</span></div>
</section>

<footer class="footer abs">
  <svg class="abs" style="left:0;top:0" width="1200" height="130" viewBox="0 0 1200 130" preserveAspectRatio="none">
    <path d="M0 40 C 350 130, 800 10, 1200 20 L1200 130 L0 130Z" fill="#8cc63f"/>
    <path d="M0 60 C 350 140, 800 20, 1200 35 L1200 130 L0 130Z" fill="#1a5585"/>
    <path d="M0 80 C 350 150, 800 40, 1200 55 L1200 130 L0 130Z" fill="#121212"/>
  </svg>
  <div class="footer-body">
    <div class="f-brand abs">Evergrove Fit</div>
    <div class="f-sub abs">Nutritional Therapy</div>
    <h5 style="left:420px">Newsletter</h5>
    <p class="f-news abs">Subscribe to us to get and receive the latest news, tips and updates.</p>
    <div class="f-field abs">Email Address</div>
    <a class="btn btn-green abs f-sign">SIGN UP</a>
    <h5 style="left:672px">Links</h5>
    <ul class="f-links abs"><li>Home</li><li>About Us</li><li>Coaching</li><li>Fitness</li><li>Nutrition</li><li>Contact Us</li></ul>
    <h5 style="left:862px">Contact Us</h5>
    <div class="f-contact abs">
      <div><svg width="18" height="20" viewBox="0 0 24 24"><path d="M12 2a7 7 0 0 0-7 7c0 5 7 13 7 13s7-8 7-13a7 7 0 0 0-7-7zm0 9.5A2.5 2.5 0 1 1 12 6.5a2.5 2.5 0 0 1 0 5z" fill="none" stroke="#8cc63f" stroke-width="1.8"/></svg><span>48 Meadow Lane,<br>Greenfield, Westvale</span></div>
      <div><svg width="18" height="18" viewBox="0 0 24 24"><path d="M6.6 10.8a15 15 0 0 0 6.6 6.6l2.2-2.2a1 1 0 0 1 1-.25 11.4 11.4 0 0 0 3.6.57 1 1 0 0 1 1 1V20a1 1 0 0 1-1 1A17 17 0 0 1 3 4a1 1 0 0 1 1-1h3.5a1 1 0 0 1 1 1c0 1.25.2 2.45.57 3.57a1 1 0 0 1-.25 1z" fill="none" stroke="#8cc63f" stroke-width="1.8"/></svg><span>(555) 013 2046</span></div>
      <div><svg width="20" height="16" viewBox="0 0 24 18"><rect x="1" y="1" width="22" height="16" fill="none" stroke="#8cc63f" stroke-width="1.8"/><path d="m1 1 11 9 11-9" fill="none" stroke="#8cc63f" stroke-width="1.8"/></svg><span>info@evergrovefit.com</span></div>
    </div>
    <div class="copyright abs">Copyright © 2019 All Rights are Reserved.</div>
    <div class="social abs"><i></i><i class="on"></i><i></i><i></i></div>
  </div>
</footer>

</body>
</html>
```